Podcast Cover Art Design for Divorce Support

Need a podcast cover art design for new podcast that will cover Emotional Divorce Support and Recovery topics. People are lost, confused. They are looking for help during the confusion and heartbreak. Main Title is "Quiet Harbor Podcast". Subtitle is "Finding Your Steady Ground". We want a design that is encouraging yet not overly "happy". We also want to convey kindness, clarity, and strength, if possible. Our logo colors use grey and red though we aren't tied to those colors for the podcast. Logo may be used on the podcast but not required. Final image should be 3000x3000px. Our logo uses Montserrat-Medium and Multi-SemiBold. Not necessary but available if you want to use it.

```html
<!DOCTYPE html>
<html lang="en">
<head>
<meta charset="utf-8">
<title>Quiet Harbor Podcast — Cover Art</title>
<link rel="stylesheet" href="https://fonts.googleapis.com/css2?family=Montserrat:wght@500;600;700&family=Yellowtail&display=swap">
<style>
  :root {
    --stage-bg: #e3e7ec;
    --stone-light: #f1f1f1;
    --stone-mid: #dcdcdc;
    --heart-red: #e30613;
    --heart-wash: rgba(227, 6, 19, 0.16);
    --band-red: #e60000;
    --ink: #0d0d0d;
    --paper-white: #ffffff;
  }
  * { margin: 0; padding: 0; box-sizing: border-box; }
  html, body {
    width: 1200px;
    height: 840px;
    overflow: hidden;
    background: var(--stage-bg);
  }
  .cover {
    position: absolute;
    left: 220px;
    top: 40px;
    width: 760px;
    height: 760px;
    overflow: hidden;
    background: radial-gradient(ellipse at 45% 40%, var(--stone-light) 0%, #e9e9e9 55%, var(--stone-mid) 100%);
    box-shadow: 0 14px 30px rgba(0, 0, 0, 0.12);
  }
  .heart-art {
    position: absolute;
    left: 100px;
    top: 70px;
    width: 560px;
    height: 530px;
    background: radial-gradient(ellipse at 50% 45%, rgba(255, 255, 255, 0) 0%, rgba(255, 255, 255, 0) 48%, var(--heart-wash) 68%, rgba(227, 6, 19, 0) 80%);
  }
  .cover__band {
    position: absolute;
    inset: 0;
    width: 760px;
    height: 760px;
  }
  .torn-band { fill: var(--band-red); }
  .torn-edge {
    fill: none;
    stroke: var(--paper-white);
    stroke-width: 3;
  }
  .title {
    position: absolute;
    left: 10px;
    width: 760px;
    text-align: center;
    white-space: nowrap;
  }
  .title__main {
    top: 196px;
    font-family: "Montserrat", sans-serif;
    font-weight: 600;
    font-size: 92px;
    line-height: 1;
    color: var(--ink);
    letter-spacing: -1px;
  }
  .title__script {
    top: 262px;
    font-family: "Yellowtail", cursive;
    font-size: 100px;
    line-height: 1;
    color: var(--heart-red);
  }
  .title__label {
    top: 390px;
    font-family: "Montserrat", sans-serif;
    font-weight: 600;
    font-size: 32px;
    line-height: 1;
    letter-spacing: 3px;
    color: var(--ink);
  }
  .tagline {
    position: absolute;
    left: 0;
    top: 692px;
    width: 760px;
    text-align: center;
    font-family: "Montserrat", sans-serif;
    font-weight: 600;
    font-size: 24px;
    line-height: 1;
    letter-spacing: 7px;
    color: var(--paper-white);
    white-space: nowrap;
  }
</style>
</head>
<body>
  <main class="cover">
    <div class="heart-art" role="img" aria-label="Hand-painted red brush-stroke heart framing the podcast title"></div>
    <svg class="cover__band" viewBox="0 0 760 760" aria-hidden="true">
      <path class="torn-band"
        d="M0 667 L40 664 L78 666 L110 660 L150 662 L185 656 L210 658 L240 650 L270 652 L300 646 L330 640 L352 644 L372 634 L392 640 L415 636 L440 643 L470 640 L500 646 L540 643 L580 650 L620 648 L660 651 L700 648 L735 652 L760 648 L760 760 L0 760 Z"/>
      <path class="torn-edge"
        d="M0 667 L40 664 L78 666 L110 660 L150 662 L185 656 L210 658 L240 650 L270 652 L300 646 L330 640 L352 644 L372 634 L392 640 L415 636 L440 643 L470 640 L500 646 L540 643 L580 650 L620 648 L660 651 L700 648 L735 652 L760 648"/>
    </svg>
    <h1 class="title title__main">Quiet</h1>
    <p class="title title__script">Harbor</p>
    <p class="title title__label">Podcast</p>
    <p class="tagline">Finding Your Steady Ground</p>
  </main>
</body>
</html>
```